High end Electrical/home automation Business Card

Need a card for a high end electrical and home automation company utilising the existing logo.
Phone
Email
Website

Like black look with raised detail. Don’t necessarily need to keep colour of logo it could be made grayscale or white etc

Target Market(s)

High end clients

Contact Information for Business Card

Brightmoor Electrical

Requirements
Must have
• Logo, phone, email, website, address

High end look
Nice to have
• Black background card
Raised font
Should not have
• Lots of colour

```html
<!DOCTYPE html>
<html lang="en">
<head>
<meta charset="utf-8">
<title>Brightmoor Electrical – Business Card</title>
<link href="https://fonts.googleapis.com/css2?family=Lato:wght@300;400;700&display=swap" rel="stylesheet">
<style>
  :root {
    --backdrop: #2a2a2b;
    --card: #141414;
    --card-edge: #0c0c0c;
    --silver: #d4d4d6;
    --silver-soft: #a9a9ac;
    --emboss-light: rgba(255,255,255,0.07);
    --emboss-dark: rgba(0,0,0,0.6);
  }
  * { margin: 0; padding: 0; box-sizing: border-box; }
  html, body {
    width: 1200px; height: 1017px; overflow: hidden;
    background: radial-gradient(ellipse at 50% 40%, #333335 0%, var(--backdrop) 70%);
    font-family: "Lato", sans-serif;
  }
  .card {
    position: absolute;
    width: 560px; height: 320px;
    background: var(--card);
    border: 1px solid var(--card-edge);
    border-radius: 3px;
    box-shadow: 0 18px 40px rgba(0,0,0,0.55);
  }
  .card--front { left: 90px; top: 130px; }
  .card--back { left: 550px; top: 540px; }

  .front-brand {
    position: absolute; inset: 0;
    display: flex; flex-direction: column; align-items: center; justify-content: center;
    gap: 22px;
  }
  .brand-dot {
    width: 46px; height: 46px; border-radius: 50%;
    background: var(--silver);
  }
  .brand-name {
    font-weight: 700; color: var(--silver);
    font-size: 30px; letter-spacing: 0.2px;
  }

  .back-emboss {
    position: absolute; right: 40px; top: 40px;
    width: 220px; height: 220px; border-radius: 50%;
    border: 14px solid #141414;
    box-shadow: -1px -1px 0 var(--emboss-light), 1px 1px 0 var(--emboss-dark),
                inset -1px -1px 0 var(--emboss-light), inset 1px 1px 0 var(--emboss-dark);
  }
  .back-content {
    position: absolute; left: 44px; top: 40px;
    color: var(--silver-soft);
  }
  .back-brand {
    font-weight: 700; color: var(--silver);
    font-size: 24px; margin-bottom: 30px;
  }
  .person-name {
    font-size: 19px; font-weight: 400; letter-spacing: 0.6px;
    color: var(--silver);
  }
  .person-role { font-size: 13px; font-weight: 300; margin-bottom: 18px; }
  .address { font-size: 13px; font-weight: 300; line-height: 1.45; margin-bottom: 14px; }
  .contact-list { list-style: none; font-size: 13px; font-weight: 300; line-height: 1.6; }
  .contact-list li { display: flex; align-items: center; gap: 9px; }
  .contact-list svg { width: 11px; height: 11px; fill: var(--silver-soft); flex: none; }
</style>
</head>
<body>
  <section class="card card--front" aria-label="Card front">
    <div class="front-brand">
      <span class="brand-dot"></span>
      <span class="brand-name">Brightmoor Electrical</span>
    </div>
  </section>

  <section class="card card--back" aria-label="Card back">
    <div class="back-emboss"></div>
    <div class="back-content">
      <div class="back-brand">Brightmoor Electrical</div>
      <div class="person-name">DANIEL HARTLEY</div>
      <div class="person-role">President</div>
      <div class="address">
        Brightmoor Electrical LLC<br>
        412 Larkspur Court<br>
        Fairbanks, Alaska 99712
      </div>
      <ul class="contact-list">
        <li>
          <svg viewBox="0 0 12 12" aria-hidden="true"><path d="M2.5 0.5l2 2.5-1.2 1.3c.8 1.7 2 2.9 3.7 3.7l1.3-1.2 2.5 2-1.3 2.2C5 10.5 1.5 7 0.3 1.8z"/></svg>
          555-014-2738
        </li>
        <li>
          <svg viewBox="0 0 12 12" aria-hidden="true"><path d="M0 2h12v8H0z M0.8 2.6L6 6.8l5.2-4.2" fill="var(--silver-soft)"/><path d="M0.8 2.8L6 6.6l5.2-3.8" stroke="#141414" stroke-width="1" fill="none"/></svg>
          info@brightmoorelectrical.com
        </li>
        <li>
          <svg viewBox="0 0 12 12" aria-hidden="true"><circle cx="6" cy="6" r="5.5"/><path d="M0.5 6h11M6 0.5c-2.4 2.8-2.4 8.2 0 11M6 0.5c2.4 2.8 2.4 8.2 0 11" stroke="#141414" stroke-width="0.9" fill="none"/></svg>
          www.brightmoorelectrical.com
        </li>
      </ul>
    </div>
  </section>
</body>
</html>
```